Custom Woodworking and Rock Design

We specialize in original, high quality, wood and rock art. It’s should be self explanatory ask questions if you need. Your team designing a logo. Furniture is custom made to order. Rocks are designed depending on consumer needs. Wood and rock can also be combined for custom work. Painted rocks on vintage wood. Custom chairs and cabinets. Artistic rocks for multiple uses:garden, magnets, custom. All ideas and requests are welcome.

Target Market(s)

All

Contact Information for Business Card

Mara Voss
Talbertstonecraft@mailbrook.net

Font styles to use
Sans Serif

Requirements
Must have
• Clear lettering
Nice to have
• Eye catching
Should not have
• Blurr

```html
<!DOCTYPE html>
<html lang="en">
<head>
<meta charset="utf-8">
<title>Talbert Stonecraft — Business Card</title>
<link rel="stylesheet" href="https://fonts.googleapis.com/css2?family=Questrial&display=swap">
<style>
  :root {
    --backdrop: #1b1b1c;
    --card: #232324;
    --card-edge: #2c2c2e;
    --silver: #a9abae;
    --white: #f2f2f2;
    --blue: #1a7fd0;
  }
  * { margin: 0; padding: 0; box-sizing: border-box; }
  html, body { width: 1200px; height: 900px; overflow: hidden; }
  body {
    background: var(--backdrop);
    font-family: "Questrial", "Century Gothic", sans-serif;
    display: flex;
    flex-direction: column;
    align-items: center;
    justify-content: center;
    gap: 40px;
  }
  .card {
    width: 630px;
    height: 360px;
    background: linear-gradient(135deg, var(--card) 0%, var(--card-edge) 100%);
    border-radius: 3px;
    box-shadow: 0 10px 30px rgba(0,0,0,.55);
    position: relative;
  }
  .card-front {
    display: flex;
    align-items: center;
    justify-content: center;
  }
  .wordmark {
    display: flex;
    align-items: center;
    gap: 14px;
    font-size: 42px;
    letter-spacing: 1px;
    white-space: nowrap;
  }
  .wordmark-mark {
    width: 16px;
    height: 16px;
    display: inline-block;
    flex: none;
  }
  .card-front .wordmark { color: var(--silver); }
  .card-front .wordmark-mark { background: var(--silver); }

  .card-back {
    display: flex;
    align-items: center;
    padding: 0 36px 0 30px;
  }
  .card-back .brand-side {
    width: 250px;
    display: flex;
    justify-content: center;
  }
  .card-back .wordmark { color: var(--white); font-size: 26px; gap: 10px; letter-spacing: .5px; }
  .card-back .wordmark-mark { background: var(--white); width: 11px; height: 11px; }
  .divider {
    width: 2px;
    height: 130px;
    background: var(--blue);
    margin: 0 26px 0 18px;
    flex: none;
  }
  .contact-side { color: var(--white); }
  .person-name {
    color: var(--blue);
    font-size: 28px;
    font-weight: 400;
    letter-spacing: 3px;
    text-transform: uppercase;
    line-height: 1.1;
  }
  .person-role {
    font-size: 16px;
    letter-spacing: 1px;
    margin-bottom: 20px;
  }
  .contact-list { list-style: none; font-size: 14px; letter-spacing: .4px; }
  .contact-list li { display: flex; align-items: center; gap: 8px; line-height: 1.7; white-space: nowrap; }
  .contact-list svg { width: 12px; height: 12px; flex: none; }
</style>
</head>
<body>
  <section class="card card-front" aria-label="Card front">
    <div class="wordmark"><span class="wordmark-mark"></span>Talbert Stonecraft</div>
  </section>

  <section class="card card-back" aria-label="Card back">
    <div class="brand-side">
      <div class="wordmark"><span class="wordmark-mark"></span>Talbert Stonecraft</div>
    </div>
    <div class="divider"></div>
    <div class="contact-side">
      <h1 class="person-name">Mara Voss</h1>
      <p class="person-role">Director</p>
      <ul class="contact-list">
        <li>
          <svg viewBox="0 0 12 12" aria-hidden="true"><path d="M3 1 L5 3.5 L4 5 Q5.5 7.5 7 8 L8.5 7 L11 9 L9.5 11 Q3 10 1 2.5 Z" fill="none" stroke="#1a7fd0" stroke-width="1"/></svg>
          +330 4172-5563
        </li>
        <li>
          <svg viewBox="0 0 12 12" aria-hidden="true"><rect x="1" y="2.5" width="10" height="7" fill="none" stroke="#1a7fd0" stroke-width="1"/><path d="M1 2.5 L6 6.5 L11 2.5" fill="none" stroke="#1a7fd0" stroke-width="1"/></svg>
          Talbertstonecraft@mailbrook.net
        </li>
        <li>
          <svg viewBox="0 0 12 12" aria-hidden="true"><circle cx="6" cy="6" r="5" fill="none" stroke="#1a7fd0" stroke-width="1"/><ellipse cx="6" cy="6" rx="2.2" ry="5" fill="none" stroke="#1a7fd0" stroke-width="1"/><path d="M1 6 H11" stroke="#1a7fd0" stroke-width="1"/></svg>
          www.talbertstonecraft.com
        </li>
      </ul>
    </div>
  </section>
</body>
</html>
```